Vantiqo custom business card design

Need a authentic, innovative business card design for a new mobile app business. I am uploading a few screen images from our app for you to view. I would like app design theme to match business card design. I can also send logo images.

```html
<!DOCTYPE html>
<html lang="en">
<head>
<meta charset="utf-8">
<title>Vantiqo business card</title>
<link rel="stylesheet" href="https://fonts.googleapis.com/css2?family=Lato:wght@400;700;900&display=swap">
<style>
  :root {
    --bg: #5c5c5c;
    --purple: #5f008b;
    --ink: #1e1e1e;
    --paper: #ffffff;
    --shadow: rgba(0, 0, 0, 0.45);
  }
  * { margin: 0; padding: 0; box-sizing: border-box; }
  html, body { width: 1200px; height: 802px; overflow: hidden; background: var(--bg); }
  body { position: relative; font-family: "Lato", sans-serif; }

  .card {
    position: absolute;
    top: 274px;
    width: 442px;
    height: 264px;
    overflow: hidden;
    box-shadow: 2px 3px 6px var(--shadow);
  }
  .card--front { left: 136px; background: var(--purple); }
  .card--back { left: 624px; background: var(--paper); }

  .front-panel {
    position: absolute; left: 0; top: 0; bottom: 0; width: 120px;
    background: var(--ink);
  }
  .front-badge {
    position: absolute; left: 0; top: 0;
    width: 264px; height: 264px; border-radius: 50%;
    background: var(--paper);
    display: flex; align-items: center; justify-content: center;
  }
  .brand {
    font-family: "Lato", sans-serif;
    font-weight: 900;
    color: var(--ink);
    letter-spacing: 0.5px;
  }
  .front-badge .brand { font-size: 38px; }

  .holder {
    position: absolute; right: 22px; top: 30px; text-align: right; color: var(--paper);
  }
  .holder__name { font-weight: 700; font-size: 17px; letter-spacing: 0.4px; line-height: 1.1; }
  .holder__role { font-size: 12px; line-height: 1.2; }

  .contacts {
    position: absolute; right: 22px; top: 141px; list-style: none;
    color: var(--paper); font-size: 12.3px; text-align: right;
  }
  .contacts li { display: flex; justify-content: flex-end; align-items: center; gap: 3px; height: 16px; }
  .contacts svg { width: 10px; height: 10px; fill: var(--paper); }

  .address {
    position: absolute; right: 25px; top: 214px; text-align: right;
    color: var(--paper); font-size: 12.3px; line-height: 16px; font-style: normal;
  }

  .back-mark {
    position: absolute; left: 0; right: 0; top: 0; bottom: 0;
    display: flex; align-items: center; justify-content: center; gap: 10px;
  }
  .back-mark__dot { width: 22px; height: 22px; border-radius: 50%; background: var(--purple); }
  .back-mark .brand { font-size: 40px; }
</style>
</head>
<body>
  <section class="card card--front">
    <div class="front-panel"></div>
    <div class="front-badge"><span class="brand">Vantiqo</span></div>

    <div class="holder">
      <div class="holder__name">DARIAN HOLT</div>
      <div class="holder__role">Managing Director</div>
    </div>

    <ul class="contacts">
      <li>055-210 348 617
        <svg viewBox="0 0 10 10" aria-hidden="true"><path d="M1 3.5C1 2 2.5 1.5 5 1.5S9 2 9 3.5L7.3 4.2 6.8 3.2H3.2L2.7 4.2ZM2.3 5h5.4l.8 3.5h-7Z"/></svg>
      </li>
      <li>055-210 348 617
        <svg viewBox="0 0 10 10" aria-hidden="true"><path d="M2.5 0.5h5v9h-5Zm1 1v6h3v-6Z"/></svg>
      </li>
      <li>hello@vantiqo.app
        <svg viewBox="0 0 10 10" aria-hidden="true"><path d="M0.5 2h9v6h-9Zm1 1 3.5 2.5L8.5 3Z"/></svg>
      </li>
      <li>www.vantiqo.app
        <svg viewBox="0 0 10 10" aria-hidden="true"><circle cx="5" cy="5" r="4.5"/></svg>
      </li>
    </ul>

    <address class="address">48 Harbor Lane, Suite 12<br>Westmere, 204518</address>
  </section>

  <section class="card card--back">
    <div class="back-mark">
      <span class="back-mark__dot"></span>
      <span class="brand">Vantiqo</span>
    </div>
  </section>
</body>
</html>
```